Flyer / Small Safety "Poster" (A4 or 8.5x11" paper)

We're looking to create a series of safety signs for woodworkers to print on home printers using standard sized paper (A4 or 8.5x11" depending on where they are), or possibly to have printed on 17x22" paper.
Currently we want only the first one, but keep in mind that all should work together.
They need: Simple graphic. Bold Text. Company logo. Use company colors (orange, black, white.)
To begin, we will start with a single sign for hearing protection. Graphic or clip art to portray either ear plugs or ear-muff design. Text to say, "Hearing Protection is a Sound Investment."

Target Market(s)

USA Woodworkers & CNC Machinists - Male, 20-65 years old

Font styles to use
Sans Serif

Colors
f37122

Requirements
Must have
• Client logo
Nice to have
• Use client colors of black, white, & orange

```html
<!DOCTYPE html>
<html lang="en">
<head>
<meta charset="utf-8">
<title>Hearing Protection Safety Sign</title>
<link rel="stylesheet" href="https://fonts.googleapis.com/css2?family=Montserrat:wght@700;800;900&display=swap">
<style>
  :root {
    --backdrop: #9a9a9c;
    --frame: #263646;
    --paper: #ffffff;
    --orange: #f37122;
    --ink: #0d0d0d;
    --pill: #111111;
    --art-light: #f69a52;
    --art-dark: #e0631a;
  }
  html, body {
    margin: 0;
    padding: 0;
    width: 1200px;
    height: 1200px;
    overflow: hidden;
    background: var(--backdrop);
    font-family: "Montserrat", sans-serif;
  }
  .sign {
    position: absolute;
    left: 218px;
    top: 98px;
    width: 778px;
    height: 1004px;
    background: var(--frame);
  }
  .sign-paper {
    position: absolute;
    left: 22px;
    top: 22px;
    width: 734px;
    height: 966px;
    background: var(--paper);
  }
  .sign-field {
    position: absolute;
    left: 14px;
    top: 14px;
    width: 706px;
    height: 844px;
    background: var(--orange);
    overflow: hidden;
  }
  .headline {
    position: absolute;
    margin: 0;
    line-height: 1;
    font-weight: 900;
    white-space: nowrap;
  }
  .headline--hearing {
    left: 20px;
    top: 18px;
    font-size: 82px;
    color: var(--ink);
    letter-spacing: -1px;
  }
  .speaker-icon {
    position: absolute;
    left: 478px;
    top: 22px;
    width: 112px;
    height: 82px;
  }
  .headline--protection {
    left: 20px;
    top: 112px;
    font-size: 63px;
    font-weight: 800;
    color: var(--paper);
  }
  .headphone-art {
    position: absolute;
    left: 220px;
    top: 190px;
    width: 276px;
    height: 462px;
    border-radius: 120px 120px 90px 90px;
    background: radial-gradient(ellipse at 50% 60%, var(--art-light), var(--art-dark));
  }
  .headline--sound {
    left: 28px;
    top: 680px;
    font-size: 106px;
    color: var(--paper);
    letter-spacing: -1px;
  }
  .headline--sound .accent { color: var(--ink); }
  .headline--investment {
    left: 28px;
    top: 774px;
    font-size: 88px;
    color: var(--paper);
    letter-spacing: 0;
  }
  .web-pill {
    position: absolute;
    left: 14px;
    top: 888px;
    width: 496px;
    height: 44px;
    border-radius: 22px;
    background: var(--pill);
    display: flex;
    align-items: center;
  }
  .web-pill__icon {
    width: 88px;
    height: 44px;
    border-radius: 22px;
    background: var(--orange);
    display: flex;
    align-items: center;
    justify-content: center;
  }
  .web-pill__url {
    margin-left: 30px;
    color: var(--paper);
    font-size: 24px;
    font-weight: 700;
  }
  .brand {
    position: absolute;
    left: 540px;
    top: 876px;
    display: flex;
    align-items: center;
    gap: 10px;
  }
  .brand__mark {
    width: 18px;
    height: 18px;
    background: var(--ink);
  }
  .brand__name {
    font-size: 23px;
    font-weight: 800;
    line-height: 1.05;
    color: var(--ink);
  }
</style>
</head>
<body>
  <main class="sign">
    <div class="sign-paper">
      <section class="sign-field">
        <h1 class="headline headline--hearing">HEARING</h1>
        <svg class="speaker-icon" viewBox="0 0 120 90" aria-hidden="true">
          <path d="M4 30 H26 L54 8 V82 L26 60 H4 Z" fill="#ffffff"/>
          <path d="M68 30 Q78 45 68 60" fill="none" stroke="#ffffff" stroke-width="7" stroke-linecap="round"/>
          <path d="M82 18 Q100 45 82 72" fill="none" stroke="#ffffff" stroke-width="7" stroke-linecap="round"/>
          <path d="M96 6 Q122 45 96 84" fill="none" stroke="#ffffff" stroke-width="7" stroke-linecap="round"/>
        </svg>
        <p class="headline headline--protection">PROTECTION</p>
        <div class="headphone-art" role="img" aria-label="Line drawing of over-ear hearing protection muffs"></div>
        <p class="headline headline--sound">IS A <span class="accent">SOUND</span></p>
        <p class="headline headline--investment">INVESTMENT</p>
      </section>
      <div class="web-pill">
        <span class="web-pill__icon">
          <svg width="24" height="24" viewBox="0 0 24 24" aria-hidden="true">
            <g fill="none" stroke="#ffffff" stroke-width="2">
              <circle cx="12" cy="12" r="10"/>
              <ellipse cx="12" cy="12" rx="4.5" ry="10"/>
              <path d="M2 12 H22 M4 7 H20 M4 17 H20"/>
            </g>
          </svg>
        </span>
        <span class="web-pill__url">www.shopcraftsupply.com</span>
      </div>
      <div class="brand">
        <span class="brand__mark"></span>
        <span class="brand__name">SHOPCRAFT<br>SUPPLY</span>
      </div>
    </div>
  </main>
</body>
</html>
```